International Clinical Software Company needs a new business card design

We are looking for a new business card design for our company that has recently expanded into the UK market, making us a multinational company.
After having rebranded our website and produced a new style guide, we are looking for a business card that is creative and attention grabbing, while being consistent with the style and colour scheme used on the new website, www.plumvora.example
We produce care management technology for the aged care market, but the main aspect we aim to communicate is the human element of our software, and the way it assists in providing better care for aged people, and stronger relationships between aged people and the staff that care for them.
Our current business card is a dark green with gold text, which makes the text quite difficult to read, not very aesthetically appealing and the colour scheme looks quite dated.
We would like something fresh and modern, that can still be colourful but doesn't use large blocks of dark colour, and uses the colours within our logo.
Something tying in with the leaves that are used in our logo could work quite nicely, along with the Autumn/Fall colours of soft greens, yellows and reds (also in our existing logo). However also happy to look at fresh, completely out of the box ideas we may not have yet considered.
Target Market(s)
The people that receive this business card work in the aged card or health industry and are either corporate/management level staff or clinical (Registered Nurses, care workers etc.)
Industry/Entity Type
Health Product
Contact Information for Business Card
Company Name - BrindlewayCare
Company locations: United Kingdom, Australia, New Zealand
Staff Details:
Staff name: Derek Mallow
Staff job title: Executive Chairman
Staff email: d.mallow@plumvora.example
Office phone number: 01742 918576
Font styles to use
Other font styles liked:
- Calibri
Requirements
Must have
- Must include the BrindlewayCare brand name in it's current font
- Must include logo (3 leaves in gold circle)
- Must include Business Card Details
Nice to have
- Elements of gold
- White space
- Something autumn themed but not too cliched
Should not have
- No blue - used by a major competitor and we would like to differentiate from them
- Large blocks of dark green colour (the green that appears in our leaves on the logo on our current business card is the background colour and it is far too dark)

```html
<!DOCTYPE html>
<html lang="en">
<head>
<meta charset="utf-8">
<title>BrindlewayCare – Business Card</title>
<link rel="stylesheet" href="https://fonts.googleapis.com/css2?family=Source+Sans+3:wght@400;600;700&display=swap">
<style>
  :root {
    --backdrop: #eeeeec;
    --card: #f4f4f3;
    --gold: #9e8a5f;
    --gold-soft: #b7a47a;
    --berry: #a3194f;
    --ink: #555558;
    --rule: #b9b9b9;
    --leaf-green: rgba(196, 214, 196, 0.45);
    --leaf-yellow: rgba(226, 224, 190, 0.5);
    --leaf-pink: rgba(232, 196, 206, 0.5);
  }
  * { margin: 0; padding: 0; box-sizing: border-box; }
  html, body {
    width: 1105px;
    height: 1200px;
    overflow: hidden;
    background: var(--backdrop);
    font-family: "Source Sans 3", sans-serif;
  }
  .business-card {
    position: absolute;
    left: 52px;
    top: 315px;
    width: 1000px;
    height: 570px;
    background: var(--card);
    overflow: hidden;
  }
  .decor-field {
    position: absolute;
    right: 0;
    top: 0;
    width: 352px;
    height: 570px;
    background:
      radial-gradient(ellipse 55% 30% at 70% 25%, var(--leaf-green), transparent 70%),
      radial-gradient(ellipse 50% 25% at 55% 55%, var(--leaf-yellow), transparent 70%),
      radial-gradient(ellipse 55% 22% at 50% 80%, var(--leaf-pink), transparent 70%);
  }
  .brand-mark {
    position: absolute;
    left: 178px;
    top: 54px;
    width: 130px;
    height: 130px;
    border-radius: 50%;
    background: var(--gold-soft);
  }
  .brand-name {
    position: absolute;
    left: 63px;
    top: 198px;
    font-size: 58px;
    font-weight: 400;
    color: var(--gold);
    letter-spacing: 0.5px;
    line-height: 1;
    white-space: nowrap;
  }
  .edge-tab {
    position: absolute;
    left: -15px;
    top: 330px;
    width: 30px;
    height: 30px;
    border-radius: 50%;
    background: var(--gold);
  }
  .person-name {
    position: absolute;
    left: 63px;
    top: 310px;
    font-size: 34px;
    font-weight: 700;
    color: var(--gold);
    letter-spacing: 0.5px;
    white-space: nowrap;
  }
  .person-title {
    position: absolute;
    left: 63px;
    top: 352px;
    font-size: 27px;
    font-weight: 400;
    color: var(--berry);
    white-space: nowrap;
  }
  .contact-list {
    position: absolute;
    left: 63px;
    top: 412px;
    list-style: none;
  }
  .contact-list li {
    display: flex;
    align-items: center;
    height: 39px;
    font-size: 26px;
    color: var(--ink);
    white-space: nowrap;
  }
  .contact-list svg {
    width: 22px;
    height: 22px;
    margin-right: 14px;
    fill: var(--gold);
    flex: none;
  }
  .divider {
    position: absolute;
    left: 508px;
    top: 413px;
    width: 1.5px;
    height: 106px;
    background: var(--rule);
  }
  .location-list {
    position: absolute;
    left: 536px;
    top: 412px;
    list-style: none;
  }
  .location-list li {
    height: 39px;
    line-height: 39px;
    font-size: 26px;
    color: var(--ink);
    white-space: nowrap;
  }
</style>
</head>
<body>
  <section class="business-card">
    <div class="decor-field" role="img" aria-label="Faint overlapping autumn leaf shapes in soft green, yellow and pink"></div>

    <div class="brand-mark"></div>
    <div class="brand-name">BrindlewayCare</div>

    <div class="edge-tab"></div>

    <div class="person-name">DEREK MALLOW</div>
    <div class="person-title">Executive Chairman</div>

    <ul class="contact-list">
      <li>
        <svg viewBox="0 0 24 24" aria-hidden="true"><path d="M6.6 10.8a15.1 15.1 0 0 0 6.6 6.6l2.2-2.2a1 1 0 0 1 1-.25 11.4 11.4 0 0 0 3.6.57 1 1 0 0 1 1 1V20a1 1 0 0 1-1 1A17 17 0 0 1 3 4a1 1 0 0 1 1-1h3.5a1 1 0 0 1 1 1c0 1.25.2 2.45.57 3.57a1 1 0 0 1-.25 1z"/></svg>
        01742 918576
      </li>
      <li>
        <svg viewBox="0 0 24 24" aria-hidden="true"><path d="M2 5h20l-10 7z"/><path d="M2 7l10 7 10-7v12H2z"/></svg>
        d.mallow@plumvora.example
      </li>
      <li>
        <svg viewBox="0 0 24 24" aria-hidden="true"><circle cx="12" cy="12" r="10"/><path d="M2 12h20M12 2c3 3 3 17 0 20M12 2c-3 3-3 17 0 20" fill="none" stroke="#f4f4f3" stroke-width="1.4"/></svg>
        www.plumvora.example
      </li>
    </ul>

    <div class="divider"></div>

    <ul class="location-list">
      <li>United Kingdom</li>
      <li>Australia</li>
      <li>New Zealand</li>
    </ul>
  </section>
</body>
</html>
```